Design for a real estate wev portal

Contents and features of the site
---------------------------------
Website in 5 languages: French, Dutch, English, German, Spanish.
English name of the site: Harbor Nest Place
Main purpose of the site:
- allow people to rent their house/ appartment for flatsharing purposes.
- help people wanting to find a room in flatsharing
- help people to find additional roommates for their flatsharing
Key interaction sequence:
1. I create a "group" of people who have common interest/hobbies
2. People who have the same interests/hobbies join my group
3. I look for a house/appartment to host my group
Website structure will be the following:
- Home
- Groups
-- Look for a group
--- Join a group
-- Create a group
- Properties
-- Look for a house/appartement
-- Apply
- Sales conditions
- Contact
- My account
-- My profile
-- My groups OR my properties
Your mission
------------
The client has no graphical guidelines, simply a logo (see attached).
We need a (responsive compliant) design for the following pages (we expect PSD's from you. No HTML nor CSS):
1. homepage (see example and wireframe attached)
2. properties search result list (see wireframe attached)
3. "detailed" form for properties
4. groups search result list
5. "detailed" form for groups
6. my account page
FOR THE COMPETITION step we only expect from you the design of first 2 screens.
Based on that, we will select the designer who will win the project, and will have to design the 4 remaining screens.
Target Market(s)
B2C
Industry/Entity Type
Real Estate
Number of Pages Required
5+ page
Look and feel
Each slider illustrates characteristics of the customer's brand and the style your logo design should communicate.

```html
<!DOCTYPE html>
<html lang="en">
<head>
<meta charset="utf-8">
<title>Harbor Nest Place</title>
<link href="https://fonts.googleapis.com/css2?family=Montserrat:wght@500;600;700&family=Open+Sans:wght@400;600;700&display=swap" rel="stylesheet">
<style>
:root{
  --teal:#1b9bad;
  --green:#67b846;
  --dark:#2b2b2b;
  --text:#6b6b6b;
  --line:#d9d9d9;
  --gray:#f1f1f1;
  --white:#fff;
}
*{box-sizing:border-box;margin:0;padding:0}
html,body{width:1200px;height:2397px;overflow:hidden;background:var(--white)}
body{position:relative;font-family:"Open Sans",Arial,sans-serif;color:var(--text)}
.abs{position:absolute}
.head-font{font-family:"Montserrat",Arial,sans-serif}

/* header */
.topbar{left:0;top:0;width:1200px;height:88px;background:var(--white)}
.main-nav{left:97px;top:34px;display:flex;gap:26px;font:600 15px "Montserrat",sans-serif;color:var(--dark)}
.main-nav .active{color:var(--green)}
.user-nav{right:97px;top:36px;display:flex;gap:10px;align-items:center;font:600 14px "Montserrat",sans-serif;color:var(--dark)}
.user-nav .sep{color:#999}
.flag{display:inline-block;width:18px;height:12px;background:#2a3d8f;margin-right:6px;vertical-align:-1px}
.brand-box{left:470px;top:0;width:260px;height:176px;z-index:3}
.brand{display:flex;align-items:center;gap:10px;font:700 27px "Montserrat",sans-serif;color:var(--dark);white-space:nowrap}
.brand .dot{width:18px;height:18px;border-radius:50%;background:var(--green);flex:none}
.brand-box .brand{position:absolute;left:24px;top:66px;font-size:24px}

/* hero */
.hero{top:88px;width:600px;height:455px}
.hero.seek{left:0;background:var(--teal)}
.hero.owner{left:600px;background:var(--green)}
.hero h2{position:absolute;left:0;width:600px;top:92px;text-align:center;font:600 23px "Montserrat",sans-serif;color:var(--white);letter-spacing:.3px}
.card{position:absolute;top:148px;width:243px;height:247px;border:2px solid rgba(255,255,255,.85)}
.card .photo{height:183px;border-bottom:2px solid rgba(255,255,255,.85)}
.card p{text-align:center;color:var(--white);font:700 16px/22px "Open Sans",sans-serif;padding-top:8px}

/* listings */
.listings{left:0;top:543px;width:1200px;height:588px;background:var(--gray)}
.col-title{font:600 22px "Montserrat",sans-serif;color:var(--dark);padding-bottom:18px;border-bottom:1px solid var(--line);width:470px}
.item{position:absolute;width:470px;height:152px}
.thumb{position:absolute;left:0;top:0;width:189px;height:152px;background:var(--white);border:1px solid var(--line);padding:8px}
.thumb div{width:100%;height:100%}
.item .info{position:absolute;left:217px;top:4px;width:253px}
.item h3{font:600 16px "Montserrat",sans-serif;color:var(--dark);margin-bottom:12px}
.item .desc{font-size:12.5px;line-height:18px;margin-bottom:10px}
.ticks{list-style:none;font-size:12.5px}
.ticks li{display:flex;align-items:center;gap:8px;margin-bottom:17px}
.ticks svg{flex:none}
.btn-outline{position:absolute;height:40px;border:1px solid #c9c9c9;background:var(--white);display:flex;align-items:center;justify-content:center;font:700 12px "Montserrat",sans-serif;color:var(--green)}

/* selling points */
.points{left:0;top:1131px;width:1200px;height:262px;background:var(--white)}
.point{position:absolute;top:52px;width:470px}
.point svg{position:absolute;left:0;top:0}
.point h3{margin-left:85px;font:600 22px/30px "Montserrat",sans-serif;color:var(--dark);padding-bottom:14px;border-bottom:1px solid var(--line)}
.point p{margin:18px 0 0 85px;font-size:12.5px;line-height:23px}

/* faq */
.faq{left:0;top:1393px;width:1200px;height:601px;background:var(--gray)}
.faq h2{position:absolute;top:44px;width:1200px;text-align:center;font:600 23px "Montserrat",sans-serif;color:var(--dark)}
.faq-row{position:absolute;left:99px;width:1002px;height:69px;background:var(--white);border:1px solid var(--line);display:flex}
.faq-row .num{width:69px;flex:none;display:flex;align-items:center;justify-content:center;font:700 34px "Montserrat",sans-serif;color:var(--white)}
.faq-row .num.g{background:var(--green)}
.faq-row .num.t{background:var(--teal)}
.faq-row p{padding:12px 18px;font-size:12.5px;line-height:23px}
.faq-row b{color:var(--green);font-weight:700;font-size:12px}

/* bands */
.band{top:1994px;width:600px;height:71px;display:flex;align-items:center;justify-content:center;gap:22px;font:600 23px "Montserrat",sans-serif;color:var(--white)}
.band.search{left:0;background:var(--green)}
.band.tools{left:600px;background:var(--teal)}

/* footer */
.footer{left:0;top:2065px;width:1200px;height:332px;background:var(--white)}
.footer .brand{position:absolute;left:88px;top:102px;font-size:26px}
.fcol{position:absolute;top:58px}
.fcol h4{font:600 16px "Montserrat",sans-serif;color:var(--dark);margin-bottom:22px}
.links{list-style:none;font-size:12px;line-height:21.5px}
.fcol .note{font-size:12px;line-height:19px;width:230px}
.email{margin-top:16px;width:255px;height:37px;border:1px solid #c9c9c9;font-size:12px;color:#aaa;padding:10px 12px}
.subscribe{margin-top:16px;width:95px;height:32px;background:var(--green);color:var(--white);font:600 11px "Open Sans",sans-serif;display:flex;align-items:center;justify-content:center}
.contact-list{list-style:none;font-size:12px;line-height:18px}
.contact-list li{display:flex;gap:14px;margin-bottom:16px}
.contact-list svg{flex:none;margin-top:2px}
.foot-line{left:99px;top:265px;width:1002px;height:1px;background:var(--line)}
.copy{left:99px;top:291px;font-size:12px}
.social{right:99px;top:281px;display:flex;gap:10px}
.social span{width:33px;height:33px;border:1px solid #bcbcbc;border-radius:50%}
</style>
</head>
<body>

<header class="abs topbar">
  <nav class="abs main-nav"><span class="active">HOME</span><span>ABOUT US</span><span>SERVICES</span><span>CONTACT</span></nav>
  <div class="abs user-nav"><span><i class="flag"></i>ENG</span><span class="sep">|</span><span>MY ACCOUNT</span><span class="sep">|</span><span>LOGIN</span></div>
</header>

<div class="abs brand-box">
  <svg width="260" height="176" viewBox="0 0 260 176" style="position:absolute;left:0;top:0"><polygon points="0,0 260,0 260,115 130,176 0,115" fill="#fff"/></svg>
  <div class="brand"><span class="dot"></span>Harbor Nest Place</div>
</div>

<section class="abs hero seek">
  <h2>SEARCHING FOR ACCOMMODATION</h2>
  <div class="card" style="left:46px"><div class="photo" role="img" aria-label="Bright furnished living room" style="background:linear-gradient(135deg,#e9e3da,#a79683)"></div><p>I want to rent a room<br>right now !</p></div>
  <div class="card" style="left:312px"><div class="photo" role="img" aria-label="Group of smiling young friends" style="background:linear-gradient(135deg,#8aa0ad,#6b4a3c)"></div><p>I want to join<br>a group</p></div>
</section>
<section class="abs hero owner">
  <h2>HAVE A HOUSE FOR RENT</h2>
  <div class="card" style="left:46px"><div class="photo" role="img" aria-label="Hands holding a phone beside a laptop and coffee" style="background:linear-gradient(135deg,#b9a694,#4d3c33)"></div><p>I want to<br>Advertise!</p></div>
  <div class="card" style="left:311px"><div class="photo" role="img" aria-label="Flatmates cooking together in a kitchen" style="background:linear-gradient(135deg,#d9d4cc,#8d7f70)"></div><p>Why is flatsharing<br>interesting for me ?</p></div>
</section>

<section class="abs listings">
  <div class="abs" style="left:99px;top:50px"><div class="col-title">GROUPS</div></div>
  <div class="abs" style="left:631px;top:50px"><div class="col-title">HOUSES</div></div>

  <div class="item" style="left:99px;top:127px">
    <div class="thumb"><div role="img" aria-label="Friends preparing food together" style="background:linear-gradient(135deg,#c9b79f,#7a5c48)"></div></div>
    <div class="info"><h3>A NICE GROUP</h3><p class="desc">Young workers, seeking for accomodation downtown.</p>
      <ul class="ticks"><li><svg width="10" height="8" viewBox="0 0 10 8"><path d="M1 4l3 3 5-6" stroke="#67b846" stroke-width="2" fill="none"/></svg>Average age: 35</li><li><svg width="10" height="8" viewBox="0 0 10 8"><path d="M1 4l3 3 5-6" stroke="#67b846" stroke-width="2" fill="none"/></svg>Men and Women welcome</li></ul></div>
  </div>
  <div class="item" style="left:99px;top:309px">
    <div class="thumb"><div role="img" aria-label="Group of young students" style="background:linear-gradient(135deg,#b5b9bf,#5a4339)"></div></div>
    <div class="info"><h3>ANOTHER NICE GROUP</h3><p class="desc">Young ladies, studying at University seeking for accomodation close to Riverside University</p>
      <ul class="ticks"><li><svg width="10" height="8" viewBox="0 0 10 8"><path d="M1 4l3 3 5-6" stroke="#67b846" stroke-width="2" fill="none"/></svg>Average age: 20 Y</li><li><svg width="10" height="8" viewBox="0 0 10 8"><path d="M1 4l3 3 5-6" stroke="#67b846" stroke-width="2" fill="none"/></svg>Women only</li></ul></div>
  </div>
  <div class="btn-outline" style="left:99px;top:492px;width:195px">SEE MORE GROUPS &gt;&gt;</div>

  <div class="item" style="left:631px;top:127px">
    <div class="thumb"><div role="img" aria-label="Detached house with a lawn" style="background:linear-gradient(180deg,#9cc0e0,#8c7b6e 55%,#5b8a3a)"></div></div>
    <div class="info"><h3>HOUSE</h3>
      <ul class="ticks"><li><svg width="10" height="8" viewBox="0 0 10 8"><path d="M1 4l3 3 5-6" stroke="#67b846" stroke-width="2" fill="none"/></svg>Town</li><li><svg width="10" height="8" viewBox="0 0 10 8"><path d="M1 4l3 3 5-6" stroke="#67b846" stroke-width="2" fill="none"/></svg>Rent per month</li><li><svg width="10" height="8" viewBox="0 0 10 8"><path d="M1 4l3 3 5-6" stroke="#67b846" stroke-width="2" fill="none"/></svg>Availability</li></ul></div>
  </div>
  <div class="item" style="left:631px;top:309px">
    <div class="thumb"><div role="img" aria-label="Apartment building under blue sky" style="background:linear-gradient(180deg,#5d8fd0,#b3603f 60%,#7b6a5e)"></div></div>
    <div class="info"><h3>APARTMENT</h3>
      <ul class="ticks"><li><svg width="10" height="8" viewBox="0 0 10 8"><path d="M1 4l3 3 5-6" stroke="#67b846" stroke-width="2" fill="none"/></svg>Town</li><li><svg width="10" height="8" viewBox="0 0 10 8"><path d="M1 4l3 3 5-6" stroke="#67b846" stroke-width="2" fill="none"/></svg>Rent per month</li><li><svg width="10" height="8" viewBox="0 0 10 8"><path d="M1 4l3 3 5-6" stroke="#67b846" stroke-width="2" fill="none"/></svg>Availability</li></ul></div>
  </div>
  <div class="btn-outline" style="left:631px;top:492px;width:195px">SEE MORE HOUSES &gt;&gt;</div>
</section>

<section class="abs points">
  <div class="point" style="left:99px">
    <svg width="60" height="52" viewBox="0 0 60 52" fill="#1b9bad"><circle cx="13" cy="12" r="7"/><circle cx="47" cy="12" r="7"/><circle cx="30" cy="15" r="9"/><path d="M2 40c0-10 5-16 11-16s8 3 8 3-4 6-4 13z"/><path d="M58 40c0-10-5-16-11-16s-8 3-8 3 4 6 4 13z"/><path d="M16 52c0-14 6-24 14-24s14 10 14 24z"/></svg>
    <h3>KEY SELLING POINTS FOR<br>THE ROOMMATES</h3>
    <p>At vero eos et accusamus et iusto odio dignissimos ducimus qui blan diis praesentium voluptatum deleniti atque corrupti quos dolores et qas molestias excepturi sint occaecati.</p>
  </div>
  <div class="point" style="left:631px">
    <svg width="58" height="52" viewBox="0 0 58 52" fill="#1b9bad"><path d="M20 10V4h18v6h-4V8H24v2z"/><rect x="2" y="12" width="54" height="38" rx="6"/><rect x="13" y="12" width="4" height="38" fill="#fff"/><rect x="41" y="12" width="4" height="38" fill="#fff"/></svg>
    <h3>KEY SELLING POINTS FOR<br>THE OWNERS</h3>
    <p>At vero eos et accusamus et iusto odio dignissimos ducimus qui blan diis praesentium voluptatum deleniti atque corrupti quos dolores et qas molestias excepturi sint occaecati.</p>
  </div>
</section>

<section class="abs faq">
  <h2>EVERYTHING YOU NEED TO KNOW ABOUT FLATSHARING</h2>
  <div class="faq-row" style="top:103px"><div class="num g">1</div><p>Consectetuer adipiscing elit, sed diam nonummy nibh euismod tincidunt ut laoreet dolore magna aliquam erat volutpat. Ut wisi enim ad minim veniam, quis nostrud exerci tation ullamcorper suscipit lobortis nisi ut aliquip ex ea commodo consequa. <b>READ MORE &gt;&gt;</b></p></div>
  <div class="faq-row" style="top:197px"><div class="num t">2</div><p>Consectetuer adipiscing elit, sed diam nonummy nibh euismod tincidunt ut laoreet dolore magna aliquam erat volutpat. Ut wisi enim ad minim veniam, quis nostrud exerci tation ullamcorper suscipit lobortis nisi ut aliquip ex ea commodo consequa. <b>READ MORE &gt;&gt;</b></p></div>
  <div class="faq-row" style="top:291px"><div class="num t">3</div><p>Consectetuer adipiscing elit, sed diam nonummy nibh euismod tincidunt ut laoreet dolore magna aliquam erat volutpat. Ut wisi enim ad minim veniam, quis nostrud exerci tation ullamcorper suscipit lobortis nisi ut aliquip ex ea commodo consequa. <b>READ MORE &gt;&gt;</b></p></div>
  <div class="faq-row" style="top:385px"><div class="num t">4</div><p>Consectetuer adipiscing elit, sed diam nonummy nibh euismod tincidunt ut laoreet dolore magna aliquam erat volutpat. Ut wisi enim ad minim veniam, quis nostrud exerci tation ullamcorper suscipit lobortis nisi ut aliquip ex ea commodo consequa. <b>READ MORE &gt;&gt;</b></p></div>
  <div class="btn-outline" style="left:502px;top:494px;width:195px">ALL QUESTIONS &gt;&gt;</div>
</section>

<div class="abs band search">
  <svg width="32" height="32" viewBox="0 0 32 32"><circle cx="13" cy="13" r="9" stroke="#fff" stroke-width="4" fill="none"/><path d="M20 20l9 9" stroke="#fff" stroke-width="5" stroke-linecap="round"/></svg>
  PRE-DEFINED SEARCHES
</div>
<div class="abs band tools">
  <svg width="32" height="32" viewBox="0 0 32 32"><path d="M4 28l14-14" stroke="#fff" stroke-width="5" stroke-linecap="round"/><circle cx="22" cy="10" r="7" fill="#fff"/><circle cx="26" cy="6" r="4" fill="#1b9bad"/></svg>
  TOOLS AND INFORMATIONS
</div>

<footer class="abs footer">
  <div class="brand"><span class="dot"></span>Harbor Nest Place</div>
  <div class="fcol" style="left:390px"><h4>INFORMATION</h4>
    <ul class="links"><li>Home</li><li>About us</li><li>Services</li><li>FAQ</li><li>Contact Us</li><li>Terms &amp; Conditions</li><li>Privacy Policy</li></ul></div>
  <div class="fcol" style="left:580px"><h4>NEWSLETTER SUBSCRIPTION</h4>
    <p class="note">Register your Email Address to get information about us</p>
    <div class="email">Email Address</div>
    <div class="subscribe">SUBSCRIBE</div></div>
  <div class="fcol" style="left:900px"><h4>CONTACT US</h4>
    <ul class="contact-list">
      <li><svg width="12" height="15" viewBox="0 0 12 15"><path d="M6 0a6 6 0 00-6 6c0 4 6 9 6 9s6-5 6-9a6 6 0 00-6-6z" fill="#67b846"/><circle cx="6" cy="6" r="2" fill="#fff"/></svg>418 Lantern Row, Suite 6 - Millbrook,<br>CA 95117</li>
      <li><svg width="13" height="13" viewBox="0 0 13 13"><path d="M3 0l2 3-1.5 1.5a8 8 0 005 5L10 8l3 2-1.5 3C6 13 0 7 0 1.5z" fill="#67b846"/></svg>555 014 2290</li>
      <li><svg width="14" height="14" viewBox="0 0 14 14"><rect x="0" y="3" width="14" height="11" rx="1" fill="#67b846"/><rect x="3" y="0" width="8" height="5" fill="#67b846"/><rect x="3" y="7" width="8" height="4" fill="#fff"/></svg>555 014 7731</li>
      <li><svg width="14" height="11" viewBox="0 0 14 11"><rect width="14" height="11" rx="1" fill="#67b846"/><path d="M1 1l6 5 6-5" stroke="#fff" stroke-width="1.4" fill="none"/></svg>hello@harbornestplace.com</li>
    </ul></div>
  <div class="abs foot-line"></div>
  <p class="abs copy">Copyrights © 2016, Harbor Nest Place. All rights reserved.</p>
  <div class="abs social"><span></span><span></span><span></span><span></span></div>
</footer>

</body>
</html>
```